Poster announcing University Web Analytics talk

We need a poster to announce an upcoming talk on Web Analytics at the local University. The event is addressed to final year students (mostly in Informatic Engineering, although other majors are wellcomed as well) who may be interested in specializing in this rising field.

The poster should present a brief list of the points we'll be addressing, as well as the place and time of the meeting. Also, it must feature our company logo (check the uploads section to find it) and our website url: http://www.brasslanternworks.net.

Texts for the poster:

Headline: "Get specialized in Web & Mobile Analytics"

Topics that will be covered:
- Introduction to Analytics, market, work opportunities
- Know the basics of an Analytics project: planning, phases, implementation
- Job bank: bring your CV!

Event information: "Thursday 20th June at the Facultad de Cartografía, Universidad de Valdemora". [A space to fill with the time must be provided here]

However, we'll be translating all the text to Spanish later, so we'll need a file where we can modify the text layers.
Updates

Thanks to all of you, we're receiving so many excellent works!

We had missed to include some important information on the brief - we didn't say anything about the colors, and we have been getting some designs based in dark colors. Now, it doesn't matter what colors you use, but we'd like better a brighter design (no matter if the color combination is more playful or either rather serious). This is going to be a free talk addressed to last year students, so we want to transmit a feeling of an interesting, easy and entertaining afternoon.

I hope these comments are helpful, please reach me with any question or comment. 

Thanks a lot again!
Nuria 
BL team

Target Market(s)

Final year students and graduates.

Industry/Entity Type

Bank

Requirements
Must have
• Design must be submitted in vector format, preferably .psd. We must be able to modify the text layers. Our logo (check the files section) and website url (http://www.brasslanternworks.net) must be included
Nice to have
• Illustrations making reference to Analytics (charts, statistics, code) and/or the internet will be a plus!

```html
<!DOCTYPE html>
<html lang="en">
<head>
<meta charset="utf-8">
<title>Get specialized in Web &amp; Mobile Analytics</title>
<link rel="stylesheet" href="https://fonts.googleapis.com/css2?family=Arimo:wght@400;700&display=swap">
<style>
  :root {
    --paper-top: #ffffff;
    --paper-bottom: #e6e8ea;
    --red: #e1242b;
    --red-dark: #c4161d;
    --ink: #222426;
    --muted: #6d7074;
    --brand: #2f8f92;
    --brand-accent: #8cc63f;
    --art-light: #d7e6f0;
    --art-mid: #7fa7c2;
    --art-dark: #2b3b4a;
  }
  * { margin: 0; padding: 0; box-sizing: border-box; }
  html, body { width: 849px; height: 1200px; overflow: hidden; background: #ffffff; }
  .poster {
    position: relative;
    width: 849px;
    height: 1200px;
    overflow: hidden;
    font-family: "Arimo", Arial, sans-serif;
    color: var(--ink);
    background: linear-gradient(180deg, var(--paper-top) 0%, var(--paper-top) 45%, var(--paper-bottom) 100%);
  }
  .brand {
    position: absolute;
    top: 78px;
    right: 50px;
    display: flex;
    align-items: center;
    gap: 16px;
  }
  .brand-mark {
    width: 44px;
    height: 44px;
    background: var(--brand-accent);
  }
  .brand-name {
    font-size: 44px;
    font-weight: 700;
    line-height: 1;
    color: var(--brand);
  }
  .headline-band {
    position: absolute;
    top: 216px;
    left: 0;
    width: 849px;
    height: 160px;
    background: var(--red);
  }
  .headline-panel {
    position: absolute;
    top: 232px;
    left: 80px;
    right: 0;
    height: 128px;
    background: #ffffff;
    padding: 18px 0 0 32px;
  }
  .headline-lead {
    font-size: 42px;
    font-weight: 400;
    line-height: 1.1;
    color: var(--ink);
  }
  .headline-topic {
    font-size: 50px;
    font-weight: 700;
    line-height: 1.1;
    color: var(--red);
  }
  .details {
    position: absolute;
    top: 392px;
    left: 112px;
    right: 60px;
  }
  .topics-title {
    font-size: 26px;
    font-weight: 700;
    color: var(--red);
    margin-bottom: 12px;
  }
  .topics {
    list-style: none;
  }
  .topics li {
    position: relative;
    padding-left: 34px;
    font-size: 23px;
    line-height: 1.4;
    color: var(--ink);
  }
  .topics li svg {
    position: absolute;
    left: 0;
    top: 8px;
    width: 20px;
    height: 16px;
  }
  .event {
    margin-top: 26px;
    font-size: 24px;
    line-height: 1.3;
    color: var(--ink);
  }
  .event strong { color: var(--red); font-weight: 700; }
  .chart-art {
    position: absolute;
    left: 0;
    top: 660px;
    width: 849px;
    height: 490px;
    background:
      radial-gradient(ellipse at 70% 40%, rgba(225,36,43,0.35) 0%, rgba(225,36,43,0) 40%),
      radial-gradient(ellipse at 45% 60%, rgba(140,198,63,0.35) 0%, rgba(140,198,63,0) 40%),
      linear-gradient(165deg, rgba(215,230,240,0) 0%, var(--art-light) 25%, var(--art-mid) 60%, var(--art-dark) 100%);
  }
  .site-url {
    position: absolute;
    right: 48px;
    bottom: 22px;
    font-size: 16px;
    color: var(--muted);
  }
</style>
</head>
<body>
<main class="poster">
  <div class="brand">
    <span class="brand-mark"></span>
    <span class="brand-name">brass lantern works</span>
  </div>

  <div class="headline-band"></div>
  <header class="headline-panel">
    <h1 class="headline-lead">Get specialized in</h1>
    <h2 class="headline-topic">Web &amp; Mobile Analytics</h2>
  </header>

  <section class="details">
    <h3 class="topics-title">Topics that will be covered:</h3>
    <ul class="topics">
      <li><svg viewBox="0 0 20 16" aria-hidden="true"><path d="M0 6h11V1l9 7-9 7V10H0z" fill="var(--red)"/></svg>Introduction to Analytics, market, work opportunities</li>
      <li><svg viewBox="0 0 20 16" aria-hidden="true"><path d="M0 6h11V1l9 7-9 7V10H0z" fill="var(--red)"/></svg>Know the basics of an Analytics project:<br>Planning, phases, implementation</li>
      <li><svg viewBox="0 0 20 16" aria-hidden="true"><path d="M0 6h11V1l9 7-9 7V10H0z" fill="var(--red)"/></svg>Job bank: bring your CV!</li>
    </ul>
    <p class="event">On <strong>Thursday 20th June</strong><br>At <strong>The Facultad de Cartografía</strong><br>Universidad de Valdemora</p>
  </section>

  <div class="chart-art" role="img" aria-label="Tablet lying at an angle showing a rising 3D bar chart in green, yellow, orange and red with a red upward arrow over data tables"></div>

  <p class="site-url">www.brasslanternworks.net</p>
</main>
</body>
</html>
```